Business Cards for new orthopaedic surgery practice

My husband and I are starting our own orthopaedic surgery practice. We are looking for a business card that is uniform, but one will have my name/title and the other will have his. You can just create one design with my name on it for now. But when I choose your design as the winning design I will ask that you add another copy with his name/title.

We are looking for classy, simple, elite all in one. We like dark blues/a little gold/yellow. Something that goes with our logo. We want our logo incorporated. Here is all the info you need:
Business name: RV Bone & Vitality Center
Location: 38517 North Willowmere Ave
Alder Cove, FL 34882
Phone: 954-218-4063
Fax: 954-582-7341
Email: info@myrvbonecare.example

Names: Lydia Vance, M.D.
Board Certified Hand and Upper Extremity Surgeon

Ebo Dansu, M.D.
Board Certified Hip & Knee Replacement/General Orthopaedic Surgeon

Can decide what you want to put on the back. Maybe a slogan:
Steady in Care. Centered on You

I am just going to upload our logo. The only thing is if we select you as the winning design, the location, and phone numbers may change. We will need your help to update that once fully solidified.

Industry/Entity Type

Medical

Contact Information for Business Card

Colors
0054AA
0677BA
7BADD7
CADEEF
E8F1F8
0094D4
00A9DD
6FCCEA
C7EBF8
E9F6FB

Requirements
Must have
• class, appeal,
Should not have
• We want to air on the side of masculine if we are looking at masculine vs. feminine feel. But we still want it classy, sophisticated, and something we will love

```html
<!DOCTYPE html>
<html lang="en">
<head>
<meta charset="utf-8">
<title>RV Bone &amp; Vitality Center — Business Card</title>
<link rel="stylesheet" href="https://fonts.googleapis.com/css2?family=Montserrat:wght@400;500;600;700&display=swap">
<style>
  :root {
    --stage: #2b2b2d;
    --navy: #1b2a52;
    --navy-emboss: #2c4175;
    --gold: #c9a25a;
    --white: #ffffff;
  }
  * { box-sizing: border-box; margin: 0; padding: 0; }
  html, body { width: 1200px; height: 875px; overflow: hidden; }
  body {
    background: var(--stage);
    font-family: "Montserrat", sans-serif;
    display: flex;
    flex-direction: column;
    align-items: center;
    justify-content: center;
    gap: 44px;
  }
  .card {
    position: relative;
    width: 640px;
    height: 366px;
    background: var(--navy);
    border-radius: 22px;
    overflow: hidden;
    box-shadow: 0 14px 30px rgba(0,0,0,.45);
  }

  /* Back side */
  .card-back .brand-mark {
    position: absolute;
    left: 50%; top: 70px;
    transform: translateX(-50%);
    display: flex; align-items: center; gap: 12px;
    color: var(--navy-emboss);
    font-weight: 600;
    font-size: 26px;
    letter-spacing: .04em;
    white-space: nowrap;
  }
  .brand-dot {
    width: 16px; height: 16px; border-radius: 50%;
    background: currentColor;
    flex: none;
  }
  .card-back .slogan {
    position: absolute;
    left: 0; right: 0; top: 250px;
    text-align: center;
    color: var(--gold);
    font-weight: 600;
    font-size: 21px;
    letter-spacing: .01em;
  }

  /* Front side */
  .card-front .brand-mark {
    position: absolute;
    right: 40px; top: 46px;
    display: flex; align-items: center; gap: 10px;
    color: var(--white);
    font-weight: 600;
    font-size: 17px;
    letter-spacing: .04em;
    white-space: nowrap;
  }
  .brand-mark .brand-dot.small { width: 11px; height: 11px; }
  .identity {
    position: absolute;
    left: 44px; top: 146px;
  }
  .identity .name {
    color: var(--gold);
    font-weight: 700;
    font-size: 27px;
    letter-spacing: .01em;
    white-space: nowrap;
  }
  .identity .title {
    color: var(--white);
    font-size: 13.5px;
    margin-top: 4px;
    white-space: nowrap;
  }
  .divider {
    position: absolute;
    left: 44px; right: 40px; top: 216px;
    height: 1px;
    background: var(--gold);
  }
  .contacts {
    position: absolute;
    left: 44px; top: 234px;
    list-style: none;
    color: var(--white);
    font-size: 14px;
    line-height: 24px;
  }
  .contacts li { display: flex; align-items: center; gap: 9px; white-space: nowrap; }
  .contacts svg { width: 13px; height: 13px; fill: var(--gold); flex: none; }
  .address {
    position: absolute;
    right: 40px; top: 234px;
    text-align: right;
    color: var(--white);
    font-size: 14px;
    line-height: 22px;
    font-style: normal;
    white-space: nowrap;
  }
  .gold-band {
    position: absolute;
    left: 0; right: 0; bottom: 0;
    height: 14px;
    background: var(--gold);
  }
</style>
</head>
<body>

  <section class="card card-back" aria-label="Card back">
    <div class="brand-mark"><span class="brand-dot"></span>RV Bone &amp; Vitality Center</div>
    <p class="slogan">Steady in Care. Centered on You</p>
  </section>

  <section class="card card-front" aria-label="Card front">
    <div class="brand-mark"><span class="brand-dot small"></span>RV Bone &amp; Vitality Center</div>

    <div class="identity">
      <h1 class="name">LYDIA VANCE, M.D.</h1>
      <p class="title">Board Certified Hand and Upper Extremity Surgeon</p>
    </div>

    <div class="divider"></div>

    <ul class="contacts">
      <li>
        <svg viewBox="0 0 24 24" aria-hidden="true"><path d="M6.6 10.8a15.5 15.5 0 0 0 6.6 6.6l2.2-2.2a1 1 0 0 1 1-.25 11.4 11.4 0 0 0 3.6.57 1 1 0 0 1 1 1V20a1 1 0 0 1-1 1A17 17 0 0 1 3 4a1 1 0 0 1 1-1h3.5a1 1 0 0 1 1 1c0 1.25.2 2.45.57 3.57a1 1 0 0 1-.25 1z"/></svg>
        954-218-4063
      </li>
      <li>
        <svg viewBox="0 0 24 24" aria-hidden="true"><path d="M6 2h12v6H6zM3 9h18a1 1 0 0 1 1 1v7h-4v5H6v-5H2v-7a1 1 0 0 1 1-1zm5 7v4h8v-4z"/></svg>
        954-582-7341
      </li>
      <li>
        <svg viewBox="0 0 24 24" aria-hidden="true"><path d="M2 5h20v14H2zm2 2v.5l8 5 8-5V7l-8 5z"/></svg>
        info@myrvbonecare.example
      </li>
    </ul>

    <address class="address">
      38517 North Willowmere Ave<br>
      Alder Cove, FL 34882
    </address>

    <div class="gold-band"></div>
  </section>

</body>
</html>
```